Poetry Book Cover Design Project

Looking for a minimalistic book cover design for a collection of poems. The book title is "Before The Lanterns Drift Away Slowly". There are three parts to the book. First covers poetry in the theme of Rage. Second love and desire. The third is strange poems. Essentially the sections are "Rage", "Desire" and the "Strange". The reason for the title "Before The Lanterns Drift Away Slowly" is as if someone is writing these till life changes towards the intended outcome as felt in each poem. I want to have the author's name "Ruvinath Kolongaswe" at the bottom. Ilustration attached.
- Minimalistic

```html
<!DOCTYPE html>
<html lang="en">
<head>
<meta charset="utf-8">
<title>Before The Lanterns Drift Away Slowly — Ruvinath Kolongaswe</title>
<link rel="stylesheet" href="https://fonts.googleapis.com/css2?family=EB+Garamond:wght@500;700&display=swap">
<style>
  :root {
    --paper: #f4f5f7;
    --title-blue: #0d55a4;
    --author-ink: #111111;
    --leaf-deep: #3f6b45;
    --leaf-mid: #6f9472;
    --leaf-light: #a9c2aa;
  }
  * { margin: 0; padding: 0; box-sizing: border-box; }
  html, body {
    width: 800px;
    height: 1200px;
    overflow: hidden;
    background: var(--paper);
  }
  .cover {
    position: relative;
    width: 800px;
    height: 1200px;
    background: linear-gradient(180deg, #f6f7f9 0%, var(--paper) 60%, #f2f3f5 100%);
    overflow: hidden;
  }
  .title {
    position: absolute;
    top: 42px;
    right: 55px;
    text-align: right;
    font-family: "EB Garamond", Garamond, serif;
    font-weight: 500;
    font-size: 122px;
    line-height: 145px;
    color: var(--title-blue);
    letter-spacing: -1px;
  }
  .title span { display: block; }
  .eucalyptus-sprig {
    position: absolute;
    left: 10px;
    top: 525px;
    width: 240px;
    height: 675px;
  }
  .author {
    position: absolute;
    left: 0;
    right: 0;
    top: 1088px;
    text-align: center;
    font-family: "EB Garamond", Garamond, serif;
    font-weight: 700;
    font-size: 40px;
    letter-spacing: 1px;
    color: var(--author-ink);
    padding-left: 0;
  }
</style>
</head>
<body>
  <main class="cover">
    <svg class="eucalyptus-sprig" viewBox="0 0 240 675" role="img" aria-label="Photograph of a eucalyptus sprig with round green leaves rising from the bottom edge">
      <defs>
        <radialGradient id="sprig-tone" cx="50%" cy="50%" r="50%">
          <stop offset="0%" stop-color="var(--leaf-deep)"/>
          <stop offset="55%" stop-color="var(--leaf-mid)"/>
          <stop offset="100%" stop-color="var(--leaf-light)" stop-opacity="0"/>
        </radialGradient>
      </defs>
      <ellipse cx="120" cy="360" rx="120" ry="360" fill="url(#sprig-tone)"/>
    </svg>

    <h1 class="title">
      <span>Before</span>
      <span>The</span>
      <span>Lanterns</span>
      <span>Drift</span>
      <span>Away</span>
      <span>Slowly</span>
    </h1>

    <p class="author">Ruvinath Kolongaswe</p>
  </main>
</body>
</html>
```